Bold, Modern, Clean "Kestrelwaymassage.com" website

Why we stand out?
We are a male and female mobile massage team. Our names are Paul and Lina. 
Kestrel Way is a Seattle based mobile massage service. Our massage is offered to the community with a goal of facilitating balance within each individual. We specialize in integrated Pain management, and sports/medical massage therapy. Every client's first assessment is attended by our male and female massage therapist team. Depending on the goals identified for an individual determines which therapist will be assigned to provide treatment, if not both.

Our passion...
Here at Kestrel Way, we have a great passion for Postural Resoration and how it is integrated into an individual's Massage treatment. We pride ourselves in being natural facilitators of healing, which takes the ego of the therapist out of the client's healing process. We strive to deliver the best massage possible by including modalities such as Neuromuscular, Myofascial release, spontaneous muscle release, postural restoration, orthopedic, and medical massage.

Our education...

We are both Graduates of Venmora, school of massage therapy. We have continuing education in medical massage, myofacial release, trigger point therapy, postural restoration, anatomy, and spontaneous muscle release. Lina is also a Certified Yoga Instructor, which amplifies her experience with flexibility and strength as it pertains to each individual. Paul's passion is Massage, stretching, and strength training to encourage postural restoration and realignment.

Our rates-

Our rates are $75/ 60 minutes, $95/ 90 minutes, and $120/ 120 minutes.

Education-
Both Lina and I worked as behavioral health professionals that specialized in life skills mentoring for youth who had experienced different types of trauma. This led us both to want to help others in a different environment, where individuals can be empowered to take responsibility over their own healing. To us, massage is a type of manipulation physical therapy, that encourages healing on many levels.

Advice to any massage client-
The most important thing to 'us', as Licenced providers is to get you on to our table to show you our skills. But a good therapist never forgets that it's not about what we do for you, but what we can facilitate for you. Your health and healing has nothing to do with us. It is yours, not ours. Identify what your goals are with any Therapist, and know what the end looks like. Progress should be tangible, such as range of motion, and decreased pain.

Lina and Paul at Kestrel Way are awesome! I recently had open heart surgery, and Lina worked on me to increase my range of motion while helping with the pinched nerve from my arm being in the same position for so long during my surgery. My wife drives a lot for work, and Paul has helped decrease her neck and lower back pain immensely. They are seriously the best therapists I have ever worked with. I would recommend them to anyone who needs anything from stress relief to a medical massage treatment. They are professional, up beat, easy going, and always on time. And, I love that they meet us where ever we like! We did a staycation recently, where they came to our hotel to give us relaxation massages. Although usually they come to our home, where we focus on pain related issues. We will continue to work with them for a long, long time.

Target Market(s)

Mobile massage therapy clients

Industry/Entity Type

Massage Therapy

Coding

Coded - Design and coding required

Number of Pages Required

1 page

Font styles to use
Serif
Sans Serif

Requirements
Must have
• Please add or remove any information that would help the presentation of our website. Our logo is posted below, please include into the website.
• Please include a contact field that includes, kestrelwaymassage@fernmail.net,
• (206) 555-0148
• We have also included our own stock photos, as well as a photo of Paul and Lina. Please include a cropped photo of both massage therapists.

```html
<!DOCTYPE html>
<html lang="en">
<head>
<meta charset="utf-8">
<title>Kestrel Way mobile massage</title>
<link href="https://fonts.googleapis.com/css2?family=Open+Sans:wght@300;400;600&family=Roboto:wght@400;500;700&display=swap" rel="stylesheet">
<style>
:root{
  --teal:#10c9b8;
  --teal-light:#19d6c6;
  --teal-btn:#0bbcae;
  --svc-h1:#0f877d;--svc-h2:#0b716a;--svc-h3:#0a5a56;--svc-h4:#084845;
  --svc-b1:#06d3c3;--svc-b2:#0bbdaf;--svc-b3:#0aa79a;--svc-b4:#0b8c82;
  --ink:#333;
  --body:#4a4a4a;
  --rule:#dcdcdc;
  --icon-grey:#8a8a8a;
  --dark:#1d1a18;
  --white:#fff;
}
*{margin:0;padding:0;box-sizing:border-box}
html,body{width:1200px;height:2643px;overflow:hidden;background:var(--white)}
body{position:relative;font-family:"Open Sans",sans-serif;color:var(--ink)}
.abs{position:absolute}

/* hero */
.hero{left:0;top:0;width:1200px;height:678px;overflow:hidden}
.hero-photo{left:0;top:0;width:1200px;height:678px;background:radial-gradient(circle at 520px 380px,#f4d7a6 0,#b9885a 14%,#6b4a33 38%,#3a2a20 70%),linear-gradient(90deg,#3a2a20,#c29a78)}
.hero-photo::after{content:"";position:absolute;inset:0;background:radial-gradient(ellipse 380px 260px at 900px 520px,rgba(232,190,160,.85),rgba(232,190,160,0) 70%),radial-gradient(ellipse 260px 300px at 1050px 180px,rgba(240,235,228,.8),rgba(240,235,228,0) 70%)}
.hero-panel{left:0;top:0}
.brand{left:120px;top:62px;display:flex;align-items:center;gap:14px}
.brand-dot{width:30px;height:30px;border-radius:50%;background:var(--teal)}
.brand-name{font-size:30px;font-weight:600;color:var(--white);line-height:1}
.nav-row{left:0;width:480px;height:83px;display:flex;align-items:center}
.nav-row.r1{top:207px}
.nav-row.r2{top:292px;background:rgba(10,110,100,.55)}
.nav-row.r3{top:374px;background:rgba(50,35,70,.45)}
.nav-row.r4{top:458px;background:rgba(70,60,55,.4)}
.nav-row.r5{top:542px;background:rgba(40,40,40,.35)}
.nav-label{position:absolute;font-size:21px;color:var(--white);letter-spacing:.3px}
.nav-line{position:absolute;height:1px;background:rgba(255,255,255,.8)}
.nav-ring{position:absolute;width:14px;height:14px;border:2px solid var(--white);border-radius:50%}
.nav-ring::after{content:"";position:absolute;left:3px;top:3px;width:4px;height:4px;border-radius:50%;background:var(--white)}
.nav-icon{position:absolute;width:24px;height:24px}

/* services */
.services{left:0;top:678px;width:1200px;height:300px;display:flex}
.svc{width:300px;display:flex;flex-direction:column}
.svc-head{height:71px;display:flex;align-items:center;justify-content:center;font-family:"Roboto",sans-serif;font-weight:700;font-size:16.5px;color:var(--white)}
.svc-body{flex:1;display:flex;flex-direction:column;align-items:center;padding-top:26px}
.svc-icon{width:46px;height:56px;border-radius:8px;background:rgba(255,255,255,.85)}
.svc-text{margin-top:26px;font-family:"Roboto",sans-serif;font-size:14.5px;line-height:26px;color:var(--white);text-align:center;width:250px}
.svc:nth-child(1) .svc-head{background:var(--svc-h1)}.svc:nth-child(1) .svc-body{background:var(--svc-b1)}
.svc:nth-child(2) .svc-head{background:var(--svc-h2)}.svc:nth-child(2) .svc-body{background:var(--svc-b2)}
.svc:nth-child(3) .svc-head{background:var(--svc-h3)}.svc:nth-child(3) .svc-body{background:var(--svc-b3)}
.svc:nth-child(4) .svc-head{background:var(--svc-h4)}.svc:nth-child(4) .svc-body{background:var(--svc-b4)}

/* shared section parts */
.section-title{left:0;width:1200px;text-align:center;font-weight:300;font-size:40px;line-height:1}
.divider{left:317px;width:564px;height:40px}
.divider::before,.divider::after{content:"";position:absolute;top:18px;width:240px;height:3px;border-top:1px solid var(--rule);border-bottom:1px solid var(--rule)}
.divider::before{left:0}.divider::after{right:0}
.divider svg{position:absolute;left:262px;top:0}
.section-text{left:140px;width:920px;text-align:center;font-size:15px;line-height:29px;color:var(--body)}
.btn{height:56px;display:flex;align-items:center;justify-content:center;font-size:16px;border-radius:4px}
.btn-solid{background:linear-gradient(180deg,var(--teal-light),var(--teal-btn));color:#083f3a;box-shadow:0 3px 0 #089488}
.btn-ghost{border:2px solid var(--teal);color:var(--ink);background:var(--white)}

/* testimonials */
.testimonials{left:0;top:1380px;width:1200px;height:417px;background:radial-gradient(ellipse 320px 200px at 420px 120px,rgba(150,110,85,.55),rgba(0,0,0,0) 70%),radial-gradient(ellipse 140px 120px at 1080px 290px,rgba(170,120,70,.6),rgba(0,0,0,0) 70%),linear-gradient(180deg,#2c2320,#1a1513)}
.testimonials .section-title{color:var(--white)}
.testimonials .divider::before,.testimonials .divider::after{border-color:rgba(255,255,255,.85)}
.quote{left:130px;width:940px;text-align:center;color:var(--white);font-size:15px;line-height:27px}
.author{left:0;width:1200px;text-align:center;color:var(--white);font-size:22px}
.dots{left:542px;top:1738px;display:flex;gap:9px}
.dots span{width:10px;height:10px;background:var(--white)}
.dots span.off{background:transparent;border:1px solid var(--white)}

/* contact + footer */
.footer{left:0;top:2225px;width:1200px;height:418px;background:linear-gradient(160deg,#3a4436 0,#2a2a28 40%,#555048 70%,#1c1a18 100%)}
.contact-bar{left:0;top:2225px;width:1200px;height:104px;background:rgba(245,245,245,.93)}
.contact-item{display:flex;align-items:center;gap:20px;top:2246px;font-size:22px;color:var(--ink)}
.contact-icon{width:62px;height:62px;background:var(--teal);border-radius:3px;display:flex;align-items:center;justify-content:center}
.foot-brand{left:0;width:1200px;top:2404px;display:flex;justify-content:center;align-items:center;gap:12px}
.foot-brand .brand-dot{width:22px;height:22px}
.foot-brand .brand-name{font-size:24px}
.social{top:2500px;left:460px;display:flex;gap:14px}
.social span{width:58px;height:58px;border:1px solid rgba(255,255,255,.85);border-radius:3px}
.social span.on{background:var(--teal);border-color:var(--teal)}
.copyright{left:0;width:1200px;top:2576px;text-align:center;font-size:14px;color:rgba(255,255,255,.9)}
</style>
</head>
<body>

<header class="hero abs">
  <div class="hero-photo abs" role="img" aria-label="Therapist giving a shoulder massage to a client lying on a treatment table in warm candlelight"></div>
  <svg class="hero-panel abs" width="520" height="678" viewBox="0 0 520 678" aria-hidden="true">
    <path d="M0 0H420C380 160 380 460 420 678H0Z" fill="rgba(20,16,14,.72)"/>
  </svg>
  <div class="brand abs"><span class="brand-dot"></span><span class="brand-name">Kestrel Way</span></div>

  <nav>
    <div class="nav-row r1 abs">
      <span class="nav-label" style="left:168px">HOME</span>
      <span class="nav-line" style="left:248px;width:148px"></span>
      <span class="nav-ring" style="left:396px"></span>
      <svg class="nav-icon" style="left:428px" viewBox="0 0 24 24"><path d="M2 12L12 3l10 9h-3v9h-5v-6h-4v6H5v-9z" fill="#fff"/></svg>
    </div>
    <div class="nav-row r2 abs">
      <span class="nav-label" style="left:150px">ABOUT US</span>
      <span class="nav-line" style="left:262px;width:150px"></span>
      <span class="nav-ring" style="left:412px"></span>
      <svg class="nav-icon" style="left:442px" viewBox="0 0 24 24"><circle cx="12" cy="7" r="5" fill="#fff"/><path d="M3 22c0-6 4-9 9-9s9 3 9 9z" fill="#fff"/></svg>
    </div>
    <div class="nav-row r3 abs">
      <span class="nav-label" style="left:142px">EDUCATION</span>
      <span class="nav-line" style="left:266px;width:148px"></span>
      <span class="nav-ring" style="left:414px"></span>
      <svg class="nav-icon" style="left:446px;width:30px" viewBox="0 0 30 24"><path d="M15 4L1 10l14 6 14-6z" fill="#fff"/><path d="M7 13v6c4 3 12 3 16 0v-6l-8 3.5z" fill="#fff"/></svg>
    </div>
    <div class="nav-row r4 abs">
      <span class="nav-label" style="left:132px">TESTIMONIAL</span>
      <span class="nav-line" style="left:274px;width:150px"></span>
      <span class="nav-ring" style="left:424px"></span>
      <svg class="nav-icon" style="left:456px;width:28px" viewBox="0 0 28 24"><ellipse cx="11" cy="9" rx="10" ry="7" fill="#fff"/><path d="M4 14l-2 6 7-4z" fill="#fff"/><ellipse cx="19" cy="14" rx="8" ry="6" fill="#fff" opacity=".85"/></svg>
    </div>
    <div class="nav-row r5 abs">
      <span class="nav-label" style="left:136px">CONTACT US</span>
      <span class="nav-line" style="left:290px;width:152px"></span>
      <span class="nav-ring" style="left:442px"></span>
      <svg class="nav-icon" style="left:470px" viewBox="0 0 24 24"><rect x="6" y="2" width="12" height="20" rx="2" fill="none" stroke="#fff" stroke-width="2"/><circle cx="12" cy="18" r="1.3" fill="#fff"/></svg>
    </div>
  </nav>
</header>

<section class="services abs">
  <div class="svc">
    <div class="svc-head">Neuromuscular</div>
    <div class="svc-body"><div class="svc-icon" role="img" aria-label="Flexed arm icon"></div><p class="svc-text">Lorem ipsum dolor sit amet, consectetur adipiscing elit, sed do eiusmod tempor incididunt ut labore et dolore magna aliqua.</p></div>
  </div>
  <div class="svc">
    <div class="svc-head">Spontaneous Muscle Release</div>
    <div class="svc-body"><div class="svc-icon" role="img" aria-label="Muscular figure icon"></div><p class="svc-text">Lorem ipsum dolor sit amet, consectetur adipiscing elit, sed do eiusmod tempor incididunt ut labore et dolore magna aliqua.</p></div>
  </div>
  <div class="svc">
    <div class="svc-head">postural restoration</div>
    <div class="svc-body"><div class="svc-icon" role="img" aria-label="Standing posture figure icon"></div><p class="svc-text">Lorem ipsum dolor sit amet, consectetur adipiscing elit, sed do eiusmod tempor incididunt ut labore et dolore magna aliqua.</p></div>
  </div>
  <div class="svc">
    <div class="svc-head">Medical Massage</div>
    <div class="svc-body"><div class="svc-icon" role="img" aria-label="Massage treatment figure icon"></div><p class="svc-text">Lorem ipsum dolor sit amet, consectetur adipiscing elit, sed do eiusmod tempor incididunt ut labore et dolore magna aliqua.</p></div>
  </div>
</section>

<section class="education">
  <h2 class="section-title abs" style="top:1032px">See Our Education</h2>
  <div class="divider abs" style="top:1088px">
    <svg width="40" height="36" viewBox="0 0 40 36"><path d="M20 6L2 14l18 8 18-8z" fill="var(--icon-grey)"/><path d="M9 18v7c6 5 16 5 22 0v-7l-11 5z" fill="var(--icon-grey)"/></svg>
  </div>
  <p class="section-text abs" style="top:1150px">We are both Graduates of Venmora, school of massage therapy. We have continuing education in medical massage, my facial release, trigger point therapy, postural restoration, anatomy, and spontaneous muscle release. Lina is also a Certified Yoga Instructor, which amplifies her experience with flexibility and strength as it pertains to each individual</p>
  <a class="btn btn-solid abs" style="left:428px;top:1272px;width:167px">READ MORE</a>
  <a class="btn btn-ghost abs" style="left:604px;top:1272px;width:168px">OUR RATE</a>
</section>

<section class="testimonials abs" role="img" aria-label="Dim photo of a back massage with a candle in the background">
</section>
<h2 class="section-title abs" style="top:1439px;color:var(--white)">What Our Clients Say</h2>
<div class="divider abs" style="top:1496px">
  <style>.tdiv::before,.tdiv::after{}</style>
  <svg width="40" height="36" viewBox="0 0 40 36"><ellipse cx="16" cy="14" rx="14" ry="10" fill="#fff"/><path d="M6 21l-3 8 10-5z" fill="#fff"/><ellipse cx="27" cy="20" rx="11" ry="8" fill="#fff"/></svg>
</div>
<p class="quote abs" style="top:1567px">Lina and Paul at Kestrel Way are awesome! I recently had open heart surgery, and Lina worked on me to increase my range of motion while helping with the pinched nerve from my arm being in the same position for so long during my surgery. My wife drives a lot for work, and Paul has helped decrease her neck and lower back pain immensely. They are seriously the best therapists I have ever worked with</p>
<p class="author abs" style="top:1666px">- Darcy T.</p>
<div class="dots abs"><span></span><span class="off"></span><span></span><span></span><span></span><span></span></div>

<section class="about">
  <h2 class="section-title abs" style="top:1849px">Know About Us</h2>
  <div class="divider abs" style="top:1905px">
    <svg width="40" height="40" viewBox="0 0 40 40"><circle cx="20" cy="11" r="8" fill="var(--icon-grey)"/><path d="M5 38c0-10 7-16 15-16s15 6 15 16z" fill="var(--icon-grey)"/></svg>
  </div>
  <p class="section-text abs" style="top:1975px">We are a male and female mobile massage team. Our names are Paul and Lina.<br>Kestrel Way is a Seattle based mobile massage service. Our massage is offered to the community with a goal of facilitating balance within each individual. We specialize in integrated Pain management, and sports/medical massage therapy. Every client's first assessment is attended by our male and female massage therapist team.</p>
  <a class="btn btn-solid abs" style="left:516px;top:2118px;width:168px">READ MORE</a>
</section>

<footer>
  <div class="footer abs" role="img" aria-label="Photo of a wooden porch with leaves and a hand-painted sign"></div>
  <div class="contact-bar abs"></div>
  <div class="contact-item abs" style="left:238px">
    <span class="contact-icon"><svg width="24" height="24" viewBox="0 0 24 24"><path d="M6 2l4 5-2 3c1 3 3 5 6 6l3-2 5 4-2 4C10 22 2 14 2 4z" fill="#fff"/></svg></span>
    <span>(206) 555-0148</span>
  </div>
  <div class="contact-item abs" style="left:580px">
    <span class="contact-icon"><svg width="26" height="20" viewBox="0 0 26 20"><rect x="1" y="1" width="24" height="18" rx="2" fill="#fff"/><path d="M2 3l11 8 11-8" fill="none" stroke="var(--teal)" stroke-width="2"/></svg></span>
    <span>kestrelwaymassage@fernmail.net</span>
  </div>
  <div class="foot-brand abs"><span class="brand-dot"></span><span class="brand-name">Kestrel Way</span></div>
  <div class="social abs"><span class="on"></span><span></span><span></span><span></span></div>
  <p class="copyright abs">© Kestrel Way mobile massage - 2015. All rights reserved.</p>
</footer>

</body>
</html>
```